we need a design for Water Bottle Lable Wrap
The product is called Calmora Springs is a restructured water. its a very healthy and rejuvenating water
we were looking at using as a tag ling Restore, Recover, Rejuvenate.

```html
<!DOCTYPE html>
<html lang="en">
<head>
<meta charset="UTF-8">
<title>Calmora Springs — Bottle Label Wrap</title>
<link rel="stylesheet" href="https://fonts.googleapis.com/css2?family=Montserrat:wght@500;600&display=swap">
<style>
  :root {
    --page: #fbfafc;
    --label-top: #c4dbf2;
    --label-mid: #e3eef9;
    --label-low: #ffffff;
    --ink: #4a5578;
    --splash-deep: #1f4f9c;
    --splash-mid: #4f86c9;
    --splash-light: #b9d4f0;
  }
  * { margin: 0; padding: 0; box-sizing: border-box; }
  html, body {
    width: 1200px;
    height: 1200px;
    overflow: hidden;
    background: var(--page);
  }
  .canvas {
    position: relative;
    width: 1200px;
    height: 1200px;
  }
  .label-wrap {
    position: absolute;
    left: 210px;
    top: 15px;
    width: 780px;
    height: 1170px;
    overflow: hidden;
    background: linear-gradient(160deg, var(--label-top) 0%, var(--label-mid) 45%, var(--label-low) 100%);
  }
  .splash-photo {
    position: absolute;
    left: 370px;
    top: 0;
    width: 410px;
    height: 100%;
    background:
      linear-gradient(90deg,
        rgba(185, 212, 240, 0) 0%,
        var(--splash-light) 14%,
        var(--splash-mid) 26%,
        var(--splash-deep) 40%,
        var(--splash-mid) 58%,
        var(--splash-light) 80%,
        rgba(220, 234, 248, 0.6) 100%);
  }
  .brand-name,
  .tagline {
    position: absolute;
    white-space: nowrap;
    color: var(--ink);
    font-family: "Montserrat", sans-serif;
    transform: translate(-50%, -50%) rotate(-90deg);
    line-height: 1;
  }
  .brand-name {
    left: 244px;
    top: 600px;
    font-size: 190px;
    font-weight: 600;
    letter-spacing: -2px;
  }
  .tagline {
    left: 361px;
    top: 604px;
    font-size: 26px;
    font-weight: 500;
    letter-spacing: 1px;
  }
</style>
</head>
<body>
  <main class="canvas">
    <section class="label-wrap">
      <div class="splash-photo" role="img" aria-label="Photograph of a clear blue water splash with droplets rising upward"></div>
      <h1 class="brand-name">Calmora</h1>
      <p class="tagline">RESTORE, RECOVER, REJUVENATE</p>
    </section>
  </main>
</body>
</html>
```